Gerald Voss Photographer

Display and sell photos. I am based in the South Coast NSW Australia.
I mainly do land scape and sea scapes and wild life. I will consider all request for photos shoots except weddings. I will also take people on photo shoots in the local area. After people purchase a photo I will organise prints and mail them out. My web page sould be secure so people can not download my photos with out payment. I would like to purchase a domain page .com. The premium $16.00 month looks good. I need to add and remove photos as required.

Target Market(s)

People who appreciate the local environment, People who would like to hang good quality natural photos in their homes or shops, motels, cafes or businesses. I will go to sporting events or family outings to photograph family members, rather then the standard family portrate.

I try to take a good photo and not use the computer I belive in takeing a good photo is the skill.

Industry/Entity Type

Domain

Font styles to use
Sans Serif

Colors

Designer to choose colors to be used in the design.

Requirements
Must have
• People must be able to see my work and not run off with it.
Clean display for all the family.

```html
<!DOCTYPE html>
<html lang="en">
<head>
<meta charset="utf-8">
<title>Gerald Voss Photographer</title>
<link rel="stylesheet" href="https://fonts.googleapis.com/css2?family=Lobster&family=Roboto:wght@400;500&display=swap">
<style>
  :root {
    --sky: #4cb8e6;
    --ink: #0d0d0d;
    --panel: rgba(20, 18, 12, 0.72);
    --strip: #141414;
    --footer: #263a45;
    --white: #ffffff;
    --button-grey: #e9e9e9;
    --text-dark: #1d2a33;
  }
  * { margin: 0; padding: 0; box-sizing: border-box; }
  html, body { width: 1200px; height: 960px; overflow: hidden; }
  body { position: relative; font-family: "Roboto", Arial, sans-serif; color: var(--white); background: var(--strip); }

  .hero-scene {
    position: absolute; left: 0; top: 0; width: 1200px; height: 707px;
    background:
      radial-gradient(ellipse at 18% 12%, rgba(255, 246, 220, 0.85) 0%, rgba(255, 240, 210, 0) 28%),
      linear-gradient(180deg, #a9b4b6 0%, #8f9a8e 24%, #6f7a4c 40%, #9a6a2c 58%, #b56d2a 72%, #6d5a22 88%, #4a4a1c 100%);
  }

  .brand { position: absolute; left: 97px; top: 0; width: 279px; height: 97px; background: var(--ink); border-bottom: 7px solid var(--sky); display: flex; align-items: center; padding-left: 29px; gap: 14px; }
  .brand-mark { width: 34px; height: 34px; border: 3px solid var(--white); }
  .brand-name { font-size: 25px; font-weight: 400; color: var(--white); }

  .main-nav { position: absolute; left: 376px; top: 0; width: 614px; height: 97px; background: var(--sky); border-bottom: 7px solid var(--ink); display: flex; align-items: center; padding-left: 27px; gap: 40px; }
  .main-nav a { color: var(--white); text-decoration: none; font-size: 16px; letter-spacing: 0.2px; }
  .main-nav a.is-current { color: var(--text-dark); }

  .cart-box { position: absolute; left: 990px; top: 0; width: 105px; height: 97px; background: var(--ink); border-bottom: 7px solid var(--sky); }
  .cart-button { position: absolute; left: 27px; top: 20px; width: 51px; height: 51px; border-radius: 50%; background: var(--white); display: flex; align-items: center; justify-content: center; }

  .hero-title { position: absolute; top: 176px; left: 0; width: 1200px; text-align: center; font-family: "Lobster", cursive; font-size: 54px; font-weight: 400; text-shadow: 0 2px 4px rgba(0,0,0,0.35); }
  .hero-sub { position: absolute; top: 260px; left: 0; width: 1200px; text-align: center; font-size: 27px; font-weight: 500; text-shadow: 0 1px 3px rgba(0,0,0,0.35); }
  .hero-button { position: absolute; left: 484px; top: 318px; width: 232px; height: 56px; border: 2px solid var(--white); display: flex; align-items: center; justify-content: center; font-size: 27px; color: var(--white); text-decoration: none; }
  .slide-controls { position: absolute; left: 573px; top: 402px; display: flex; gap: 7px; }

  .info-panel { position: absolute; top: 513px; height: 168px; background: var(--panel); }
  .info-panel.about { left: 97px; width: 492px; }
  .info-panel.blog { left: 601px; width: 493px; }
  .panel-head { height: 34px; background: var(--ink); }
  .panel-tab { display: inline-block; height: 34px; line-height: 34px; padding: 0 13px; background: var(--sky); font-size: 16px; }
  .about-portrait { position: absolute; left: 19px; top: 51px; width: 101px; height: 101px; border-radius: 50%; background: linear-gradient(160deg, #d9dde0, #9aa2a8); border: 3px solid var(--white); }
  .panel-text { position: absolute; font-size: 13px; line-height: 22px; text-align: justify; }
  .about .panel-text { left: 140px; top: 57px; width: 324px; }
  .blog-thumb { position: absolute; left: 25px; top: 62px; width: 86px; height: 78px; background: linear-gradient(180deg, #5d8a3a, #a7773f); }
  .blog-title { position: absolute; left: 131px; top: 60px; font-size: 17px; font-weight: 400; }
  .blog .panel-text { left: 131px; top: 84px; width: 324px; line-height: 18px; }

  .photo-strip { position: absolute; left: 0; top: 707px; width: 1200px; height: 162px; background: var(--strip); }
  .strip-arrow { position: absolute; top: 68px; }
  .strip-arrow.prev { left: 64px; }
  .strip-arrow.next { left: 1102px; }
  .photo-tile { position: absolute; top: 18px; width: 181px; height: 130px; }
  .tile-1 { left: 104px; background: linear-gradient(180deg, #3a77b8 0%, #5f8aa0 40%, #1f5160 100%); }
  .tile-2 { left: 302px; background: linear-gradient(135deg, #3d4a2c, #c67a2e 55%, #6b5030); }
  .tile-3 { left: 501px; background: linear-gradient(180deg, #e06a56 0%, #b56aa8 45%, #6a4a78 100%); }
  .tile-4 { left: 701px; background: linear-gradient(180deg, #4aa6d8 0%, #8fcde6 45%, #d9b88a 75%, #c9a06a 100%); }
  .tile-5 { left: 900px; background: linear-gradient(135deg, #3a3a2a, #c4a060 50%, #2a4a5a); }
  .tile-actions { position: absolute; left: 6px; top: 45px; display: flex; gap: 2px; }
  .tile-action { width: 42px; height: 38px; background: var(--button-grey); display: flex; align-items: center; justify-content: center; }
  .tile-action.is-active { background: var(--sky); }
  .tile-label { position: absolute; left: 38px; top: 92px; font-size: 12px; }

  .site-footer { position: absolute; left: 0; top: 869px; width: 1200px; height: 91px; background: var(--footer); }
  .copyright { position: absolute; left: 103px; top: 43px; font-size: 12px; }
  .social-links { position: absolute; right: 106px; top: 40px; display: flex; gap: 12px; }
  .social-links a { display: flex; align-items: center; gap: 5px; color: var(--white); text-decoration: none; font-size: 12px; }
  .social-links a::before { content: ""; width: 9px; height: 9px; border-radius: 50%; background: var(--white); }
</style>
</head>
<body>
  <div class="hero-scene" role="img" aria-label="Mountain valley landscape at sunrise with golden grass"></div>

  <header>
    <div class="brand"><span class="brand-mark"></span><span class="brand-name">Gerald Voss</span></div>
    <nav class="main-nav">
      <a class="is-current" href="#">HOME</a>
      <a href="#">ABOUT ME</a>
      <a href="#">GALLERIES</a>
      <a href="#">PORTFOLIOS</a>
      <a href="#">CONTACT US</a>
    </nav>
    <div class="cart-box">
      <a class="cart-button" href="#" aria-label="Cart">
        <svg width="26" height="22" viewBox="0 0 26 22" fill="none" stroke="#222" stroke-width="2"><path d="M1 2h4l3 12h13l3-9H7"/><circle cx="10" cy="19" r="1.6"/><circle cx="19" cy="19" r="1.6"/></svg>
      </a>
    </div>
  </header>

  <section class="hero">
    <h1 class="hero-title">Welcome to Gerald Voss</h1>
    <p class="hero-sub">Landscape and Seascapes and Wildlife Photography</p>
    <a class="hero-button" href="#">VIEW MORE</a>
    <div class="slide-controls">
      <svg width="28" height="28" viewBox="0 0 28 28" fill="none" stroke="#fff" stroke-width="2.5"><circle cx="14" cy="14" r="12"/><path d="M16 8l-6 6 6 6"/></svg>
      <svg width="28" height="28" viewBox="0 0 28 28" fill="none" stroke="#fff" stroke-width="2.5"><circle cx="14" cy="14" r="12"/><path d="M12 8l6 6-6 6"/></svg>
    </div>
  </section>

  <section class="info-panel about">
    <div class="panel-head"><span class="panel-tab">ABOUT ME</span></div>
    <div class="about-portrait" role="img" aria-label="Portrait of the photographer holding a camera"></div>
    <p class="panel-text">Lorem Ipsum is simply dummy text of the printing and typesetting industry. Lorem Ipsum has been the industry's standard dummy text ever since the 1500s, when an unknown printer took a galley of type and scrambled</p>
  </section>

  <section class="info-panel blog">
    <div class="panel-head"><span class="panel-tab">LATEST BLOG</span></div>
    <div class="blog-thumb" role="img" aria-label="Young deer in green grass"></div>
    <h2 class="blog-title">Lorem Ipsum is simply dummy text</h2>
    <p class="panel-text">Lorem Ipsum is simply dummy text of the printing and typesetting industry. Lorem Ipsum has been the industry's standard dummy text ever since the 1500s, when</p>
  </section>

  <section class="photo-strip">
    <svg class="strip-arrow prev" width="18" height="32" viewBox="0 0 18 32" fill="none" stroke="#4cb8e6" stroke-width="2.5"><path d="M16 2L3 16l13 14"/></svg>
    <div class="photo-tile tile-1" role="img" aria-label="Wooden jetty under a blue sky">
      <div class="tile-actions">
        <span class="tile-action is-active"><svg width="22" height="20" viewBox="0 0 22 20" fill="#fff"><rect x="5" y="1" width="12" height="5"/><rect x="1" y="7" width="20" height="8" rx="1"/><rect x="5" y="12" width="12" height="7" fill="#fff" stroke="#4cb8e6" stroke-width="1.5"/></svg></span>
        <span class="tile-action"><svg width="22" height="20" viewBox="0 0 26 22" fill="none" stroke="#222" stroke-width="2"><path d="M1 2h4l3 12h13l3-9H7"/><circle cx="10" cy="19" r="1.6"/><circle cx="19" cy="19" r="1.6"/></svg></span>
        <span class="tile-action"><svg width="22" height="14" viewBox="0 0 22 14"><path d="M1 7C5 1 17 1 21 7C17 13 5 13 1 7Z" fill="#111"/><circle cx="11" cy="7" r="3" fill="#e9e9e9"/></svg></span>
        <span class="tile-action"><svg width="20" height="18" viewBox="0 0 20 18" fill="#111"><path d="M10 17L2 9A4.6 4.6 0 0 1 10 3A4.6 4.6 0 0 1 18 9Z"/></svg></span>
      </div>
      <span class="tile-label">PRINT OUT</span>
    </div>
    <div class="photo-tile tile-2" role="img" aria-label="Tiger resting on a log"></div>
    <div class="photo-tile tile-3" role="img" aria-label="Pink and purple sunset over the sea"></div>
    <div class="photo-tile tile-4" role="img" aria-label="Starfish on a sandy beach"></div>
    <div class="photo-tile tile-5" role="img" aria-label="Duck taking off from water"></div>
    <svg class="strip-arrow next" width="18" height="32" viewBox="0 0 18 32" fill="none" stroke="#4cb8e6" stroke-width="2.5"><path d="M2 2l13 14L2 30"/></svg>
  </section>

  <footer class="site-footer">
    <p class="copyright">© 2014 Gerald Voss. All rights reserved</p>
    <nav class="social-links">
      <a href="#">Chirpline</a>
      <a href="#">Friendwall</a>
      <a href="#">Feedcast</a>
      <a href="#">Circlenet</a>
    </nav>
  </footer>
</body>
</html>
```